business card Calvanto

Wee need a business card design for a new compagny based on Paris
We developped innovative a platform for selling services to refresh, beautify and develop its housing.
We would like a red logo on a black background
Te final design should communicate quality service, know-how, high-end

Target Market(s)

individuals

Industry/Entity Type

Business

```html
<!DOCTYPE html>
<html lang="en">
<head>
<meta charset="utf-8">
<title>Calvanto — Business Card</title>
<link href="https://fonts.googleapis.com/css2?family=Questrial&family=Open+Sans:wght@400;700&display=swap" rel="stylesheet">
<style>
  :root {
    --backdrop: #d9d9d9;
    --card: #ffffff;
    --brand-red: #e2605a;
    --wordmark-grey: #7a7a7a;
    --text-dark: #2b2b2b;
    --rule: #8a8a8a;
    --faint: #f1f1f1;
  }
  * { box-sizing: border-box; margin: 0; padding: 0; }
  html, body {
    width: 1200px; height: 852px; overflow: hidden;
    background: var(--backdrop);
    font-family: "Open Sans", sans-serif;
  }
  .stage {
    position: relative; width: 1200px; height: 852px;
    display: flex; align-items: center; justify-content: center; gap: 50px;
  }
  .card {
    position: relative; width: 525px; height: 300px;
    background: var(--card); border-radius: 22px;
    box-shadow: 0 6px 18px rgba(0,0,0,0.18);
    overflow: hidden;
  }
  .brand {
    display: flex; align-items: center; gap: 14px;
  }
  .brand-square {
    width: 54px; height: 54px; background: var(--brand-red);
  }
  .brand-name {
    font-family: "Questrial", sans-serif;
    font-size: 48px; color: var(--wordmark-grey); line-height: 1;
    letter-spacing: 0.5px;
  }

  /* Front */
  .card-front .faint-block {
    position: absolute; right: -40px; top: -30px;
    width: 260px; height: 260px; background: var(--faint);
  }
  .card-front .brand {
    position: absolute; left: 50%; top: 50%;
    transform: translate(-50%, -50%);
  }

  /* Back */
  .card-back .brand { position: absolute; left: 30px; top: 70px; }
  .holder {
    position: absolute; right: 30px; top: 30px; text-align: right;
  }
  .holder-name { color: var(--brand-red); font-weight: 700; font-size: 15px; }
  .holder-role { color: var(--text-dark); font-size: 10.5px; margin-top: 2px; }
  .rule {
    position: absolute; height: 1.5px; background: var(--rule);
  }
  .rule-top { left: 30px; right: 30px; top: 142px; }
  .rule-bottom { left: 30px; width: 250px; top: 210px; }
  .details {
    position: absolute; list-style: none;
    font-size: 11.5px; color: var(--text-dark);
  }
  .details li { display: flex; align-items: flex-start; gap: 9px; line-height: 1.35; margin-bottom: 5px; }
  .details svg { width: 11px; height: 11px; flex: none; margin-top: 2px; fill: var(--brand-red); }
  .details-office { left: 300px; top: 158px; width: 200px; }
  .details-contact { left: 30px; top: 222px; }
  .accent { color: var(--brand-red); }
</style>
</head>
<body>
<main class="stage">

  <section class="card card-front" aria-label="Card front">
    <div class="faint-block" aria-hidden="true"></div>
    <div class="brand">
      <span class="brand-square"></span>
      <span class="brand-name">Calvanto</span>
    </div>
  </section>

  <section class="card card-back" aria-label="Card back">
    <div class="holder">
      <div class="holder-name">Your Long Name</div>
      <div class="holder-role">Managing Director</div>
    </div>
    <div class="brand">
      <span class="brand-square"></span>
      <span class="brand-name">Calvanto</span>
    </div>
    <div class="rule rule-top"></div>

    <ul class="details details-office">
      <li>
        <svg viewBox="0 0 12 12"><path d="M6 0a4 4 0 0 0-4 4c0 3 4 8 4 8s4-5 4-8a4 4 0 0 0-4-4zm0 5.6A1.6 1.6 0 1 1 6 2.4a1.6 1.6 0 0 1 0 3.2z"/></svg>
        <span>Your Commercial or office<br>address in two line</span>
      </li>
      <li>
        <svg viewBox="0 0 12 12"><circle cx="6" cy="6" r="5.2" fill="none" stroke="#e2605a" stroke-width="1.2"/><path d="M0.8 6h10.4M6 0.8c-2.6 3-2.6 7.4 0 10.4M6 0.8c2.6 3 2.6 7.4 0 10.4" fill="none" stroke="#e2605a" stroke-width="1"/></svg>
        <span>www.<span class="accent">yourwebsite</span>.com</span>
      </li>
    </ul>

    <div class="rule rule-bottom"></div>

    <ul class="details details-contact">
      <li>
        <svg viewBox="0 0 12 12"><path d="M2.5 0.5l2 2.5-1.2 1.4a7 7 0 0 0 4.3 4.3L9 7.5l2.5 2-1.5 2C5 11.5 0.5 7 0.5 2z"/></svg>
        <span>00.00.00.0000</span>
      </li>
      <li>
        <svg viewBox="0 0 12 12"><rect x="2.5" y="0.5" width="7" height="11" rx="1.2"/><rect x="3.7" y="1.8" width="4.6" height="7" fill="#fff"/></svg>
        <span>00.00.00.0000</span>
      </li>
      <li>
        <svg viewBox="0 0 12 12"><rect x="0.5" y="2" width="11" height="8"/><path d="M0.8 2.3L6 6.6l5.2-4.3" fill="none" stroke="#fff" stroke-width="1"/></svg>
        <span>yourname@yourwebsite.com</span>
      </li>
    </ul>
  </section>

</main>
</body>
</html>
```